The Vantor Codex Book Cover

"The Vantor Codex" is a book I wrote with the slogan "Unlock Performance, Spark Engagement: Master the Art of Building Winning Cultures in Today's Hybrid World". The book is designed around a methodology that's mine and that I attached. I would love to see the graphic of the methodology integrated in the design in a very subtle way. Use colors from the model but the book cover should be catchy, modern and engaging to the eye.
Overall the book is about three key elements towards success:
- (Self) Directions (purpose)
- Human experience (people and psychological safety)
- Maximize engagement
The methodology is a FLOW so flow is something that could be incorporated as well in the concept.
Low design quality
Managers and Teams

```html
<!DOCTYPE html>
<html lang="en">
<head>
<meta charset="utf-8">
<title>The Vantor Codex – Book Cover</title>
<link href="https://fonts.googleapis.com/css2?family=Montserrat:wght@300;400;600;700;800;900&display=swap" rel="stylesheet">
<style>
  :root {
    --paper: #fdfdfd;
    --ink: #050505;
    --brand-green: #05cc45;
    --map-green: #12e86a;
    --map-green-deep: #00c93a;
  }
  html, body {
    margin: 0;
    padding: 0;
    width: 933px;
    height: 1200px;
    overflow: hidden;
    background: var(--paper);
  }
  .cover {
    position: relative;
    width: 933px;
    height: 1200px;
    overflow: hidden;
    background: var(--paper);
    font-family: "Montserrat", sans-serif;
    color: var(--ink);
  }
  .corner-tab {
    position: absolute;
    left: 83px;
    top: 0;
    width: 107px;
    height: 49px;
    background: var(--brand-green);
  }
  .tagline {
    position: absolute;
    left: 72px;
    top: 90px;
    margin: 0;
    font-weight: 400;
    font-size: 21px;
    letter-spacing: 0.42em;
    text-transform: uppercase;
    white-space: nowrap;
  }
  .title {
    position: absolute;
    left: 68px;
    top: 150px;
    margin: 0;
    line-height: 1;
  }
  .title span { display: block; }
  .title-lead {
    font-weight: 800;
    font-size: 116px;
    letter-spacing: -0.01em;
  }
  .title-main {
    font-weight: 900;
    font-size: 143px;
    color: var(--brand-green);
    margin-top: -14px;
    letter-spacing: -0.02em;
  }
  .title-tail {
    font-weight: 600;
    font-size: 96px;
    margin-top: -6px;
  }
  .rule {
    position: absolute;
    left: 77px;
    top: 508px;
    width: 426px;
    height: 11px;
    background: var(--brand-green);
  }
  .flow-model {
    position: absolute;
    left: 519px;
    top: 481px;
    width: 145px;
    height: 92px;
  }
  .subtitle {
    position: absolute;
    left: 70px;
    top: 584px;
    margin: 0;
    font-weight: 700;
    font-size: 27px;
    line-height: 36px;
  }
  .byline {
    position: absolute;
    left: 73px;
    top: 742px;
    margin: 0;
    font-weight: 600;
    font-size: 27px;
  }
  .author {
    position: absolute;
    left: 72px;
    top: 790px;
    margin: 0;
    font-weight: 300;
    font-size: 60px;
    line-height: 70px;
    letter-spacing: 0.34em;
  }
  .author span { display: block; }
  .world-map {
    position: absolute;
    left: 19px;
    top: 933px;
    width: 914px;
    height: 252px;
  }
  .team-photo {
    position: absolute;
    left: 451px;
    top: 733px;
    width: 222px;
    height: 293px;
  }
</style>
</head>
<body>
<div class="cover">
  <div class="corner-tab"></div>

  <p class="tagline">Unlock Performance, Spark Engagement:</p>

  <h1 class="title">
    <span class="title-lead">THE</span>
    <span class="title-main">VANTOR</span>
    <span class="title-tail">CODEX</span>
  </h1>

  <div class="rule"></div>

  <svg class="flow-model" role="img" aria-label="Multicoloured flow methodology diagram in an infinity shape" viewBox="0 0 145 92">
    <defs>
      <linearGradient id="flowTones" x1="0" y1="0" x2="1" y2="1">
        <stop offset="0" stop-color="#ef7a86"/>
        <stop offset="0.35" stop-color="#6b5c86"/>
        <stop offset="0.6" stop-color="#5aa9c8"/>
        <stop offset="1" stop-color="#c9c77a"/>
      </linearGradient>
    </defs>
    <rect x="0" y="0" width="145" height="92" rx="46" fill="url(#flowTones)" opacity="0.75"/>
  </svg>

  <p class="subtitle">Master the Art of<br>Building Winning<br>Cultures in Today's<br>Hybrid World</p>

  <p class="byline">by</p>

  <p class="author"><span>JORIN</span><span>VASKER</span></p>

  <svg class="world-map" role="img" aria-label="Green world map spread across the lower cover" viewBox="0 0 914 252" preserveAspectRatio="none">
    <defs>
      <linearGradient id="mapTones" x1="0" y1="0" x2="1" y2="1">
        <stop offset="0" stop-color="#12e86a"/>
        <stop offset="1" stop-color="#00c93a"/>
      </linearGradient>
    </defs>
    <rect x="0" y="0" width="914" height="252" fill="url(#mapTones)" opacity="0.85"/>
  </svg>

  <svg class="team-photo" role="img" aria-label="Photo of four business people in white shirts and green ties shaking hands in a circle" viewBox="0 0 222 293">
    <defs>
      <linearGradient id="teamTones" x1="0" y1="0" x2="0" y2="1">
        <stop offset="0" stop-color="#e9ece9"/>
        <stop offset="0.45" stop-color="#9fcf6a"/>
        <stop offset="1" stop-color="#3a3d42"/>
      </linearGradient>
    </defs>
    <rect x="0" y="0" width="222" height="293" fill="url(#teamTones)"/>
  </svg>
</div>
</body>
</html>
```